Local Roofing/Construction company business needs new biz card design

We need a new business card design, current cards are from the start of this operation and generic at best. We are a local Construction Company (General Contractor) with a majority of our work originating from insurance claims-exterior finish work is the main focus (Roofs-Siding-Gutters etc). Heavily involved with homeowners and the low ball offers they receive from insurance company's after a insurable event takes place. I have attached some of our original logo file(s) below.

```html
<!DOCTYPE html>
<html lang="en">
<head>
<meta charset="utf-8">
<title>Halvorsen Builders — Business Card</title>
<link rel="stylesheet" href="https://fonts.googleapis.com/css2?family=Montserrat:wght@400;500;700&display=swap">
<style>
  :root {
    --backdrop: #151616;
    --card: #0f1e20;
    --green: #52b36b;
    --ink: #f2f2f0;
  }
  * { margin: 0; padding: 0; box-sizing: border-box; }
  html, body { width: 1200px; height: 1059px; overflow: hidden; }
  body {
    background: var(--backdrop);
    font-family: "Montserrat", sans-serif;
    position: relative;
  }
  .card {
    position: absolute;
    background: var(--card);
    border-radius: 22px;
  }
  .card--front { left: 257px; top: 89px; width: 687px; height: 390px; }
  .card--back  { left: 254px; top: 547px; width: 693px; height: 393px; }

  .brand {
    position: absolute;
    display: flex;
    align-items: center;
    gap: 12px;
    color: var(--green);
    font-weight: 700;
    text-transform: uppercase;
    white-space: nowrap;
  }
  .brand__mark {
    width: 18px; height: 18px;
    background: var(--green);
    border-radius: 3px;
    flex: none;
  }
  .card--front .brand {
    left: 50%; top: 102px;
    transform: translate(-50%, -50%);
    font-size: 34px;
    letter-spacing: 1px;
  }
  .card--back .brand {
    left: 50%; top: 196px;
    transform: translate(-50%, -50%);
    font-size: 34px;
    letter-spacing: 1px;
  }

  .person {
    position: absolute;
    right: 365px; top: 220px;
    text-align: right;
  }
  .person__name {
    color: var(--green);
    font-weight: 700;
    font-size: 23px;
    letter-spacing: 1.2px;
    line-height: 28px;
  }
  .person__role {
    color: var(--ink);
    font-size: 15.5px;
    font-weight: 500;
    letter-spacing: 0.4px;
    line-height: 20px;
  }
  .divider {
    position: absolute;
    left: 343px; top: 211px;
    width: 1.5px; height: 63px;
    background: var(--green);
  }
  .contacts {
    position: absolute;
    left: 370px; top: 204px;
    list-style: none;
  }
  .contacts li {
    display: flex;
    align-items: center;
    gap: 8px;
    height: 26px;
    color: var(--ink);
    font-size: 16px;
    letter-spacing: 0.5px;
  }
  .contacts svg { width: 12px; height: 12px; flex: none; }
  .address {
    position: absolute;
    left: 0; right: 0; top: 323px;
    text-align: center;
    color: var(--ink);
    font-size: 16px;
    letter-spacing: 0.5px;
  }
</style>
</head>
<body>
  <section class="card card--front">
    <div class="brand"><span class="brand__mark"></span>Halvorsen Builders</div>

    <div class="person">
      <div class="person__name">DANIEL MARSH</div>
      <div class="person__role">Managing Director</div>
    </div>
    <div class="divider"></div>

    <ul class="contacts">
      <li>
        <svg viewBox="0 0 12 12" aria-hidden="true"><path fill="var(--green)" d="M2.3 1 4.2 3 3.4 4.3a6.5 6.5 0 0 0 4.3 4.3L9 7.8 11 9.7 9.8 11C5 10.6 1.4 7 1 2.2Z"/></svg>
        0412 555 019
      </li>
      <li>
        <svg viewBox="0 0 12 12" aria-hidden="true"><path fill="var(--green)" d="M1 5 6 1.5 11 5v6H1Zm1.3 1 3.7 2.6L9.7 6v4H2.3Z"/></svg>
        info@halvorsenbuilders.com
      </li>
      <li>
        <svg viewBox="0 0 12 12" aria-hidden="true"><circle cx="6" cy="6" r="5.2" fill="var(--green)"/><path fill="var(--card)" d="M4 3.2c1 .2 1.5 1 1 1.8S3.4 5.6 3.6 7c-.9-.7-1.2-2.5.4-3.8Zm3.2 3c.9.1 1.6.7 1.4 1.7-.4.8-1.4 1.2-2 .6.1-.9.3-1.6.6-2.3Z"/></svg>
        www.halvorsenbuilders.com
      </li>
    </ul>

    <p class="address">1450 W Cedar Avenue Millbrook County Name 4120</p>
  </section>

  <section class="card card--back">
    <div class="brand"><span class="brand__mark"></span>Halvorsen Builders</div>
  </section>
</body>
</html>
```